i need a business card for a plumbing company in california

we are a drain cleaning , maintenance plumbing company who is starting new marketing campaign for a tatrench-less pipe installation department .

Target Market(s)

the professional who appreciates time and quality workmanship.

Industry/Entity Type

Plumbing

Colors
0655a3
ec1f27

Requirements
Must have
• the second logo needs to be included
Nice to have
• a focus on the services offered
Should not have
• any underlined words on the brief

```html
<!DOCTYPE html>
<html lang="en">
<head>
<meta charset="utf-8">
<title>Keystone Plumbing – Business Card</title>
<link rel="stylesheet" href="https://fonts.googleapis.com/css2?family=Arimo:wght@700&family=Noto+Serif:wght@400&display=swap">
<style>
  :root {
    --brand-blue: #0655a3;
    --brand-red: #ec1f27;
    --deep-blue: #0a3f86;
    --logo-grey: #77746c;
    --card-white: #f6f6f6;
    --stage: #2e2e2e;
    --text-white: #ffffff;
  }
  * { margin: 0; padding: 0; box-sizing: border-box; }
  html, body { width: 1200px; height: 997px; overflow: hidden; }
  body {
    background: var(--stage);
    position: relative;
    font-family: "Arimo", Arial, sans-serif;
  }
  .card {
    position: absolute;
    left: 250px;
    width: 700px;
    height: 400px;
    border-radius: 18px;
    overflow: hidden;
    background: var(--card-white);
  }
  .card--back { top: 60px; }
  .card--front { top: 537px; }
  .card__art { position: absolute; inset: 0; width: 100%; height: 100%; }

  .service {
    position: absolute;
    transform: translateX(-50%);
    font-weight: 700;
    font-size: 13px;
    letter-spacing: 0.3px;
    line-height: 1;
    white-space: nowrap;
    text-transform: uppercase;
  }
  .service--red { color: var(--brand-red); }
  .service--blue { color: var(--brand-blue); }

  .wordmark {
    position: absolute;
    display: flex;
    align-items: center;
    gap: 16px;
    color: var(--logo-grey);
    font-weight: 700;
    line-height: 0.95;
  }
  .wordmark__dot {
    width: 46px; height: 46px;
    border-radius: 50%;
    background: var(--brand-red);
    flex: none;
  }
  .card--back .wordmark { left: 60px; top: 250px; font-size: 50px; }
  .card--front .wordmark { left: 180px; top: 70px; font-size: 56px; }

  .person {
    position: absolute;
    right: 40px;
    top: 178px;
    text-align: right;
  }
  .person__name { color: var(--brand-red); font-size: 22px; font-weight: 700; letter-spacing: 0.5px; }
  .person__role { color: var(--brand-blue); font-size: 15px; font-weight: 700; }

  .contact {
    position: absolute;
    left: 34px;
    bottom: 26px;
    list-style: none;
    color: var(--text-white);
    font-family: "Noto Serif", Georgia, serif;
    font-size: 18px;
    line-height: 30px;
  }
  .contact li { display: flex; align-items: center; gap: 12px; }
  .contact svg { width: 14px; height: 14px; flex: none; fill: var(--text-white); }
</style>
</head>
<body>

<!-- Back of card: services -->
<section class="card card--back" aria-label="Card back with services">
  <svg class="card__art" viewBox="0 0 700 400" aria-hidden="true">
    <path d="M0,0 H700 V80 Q350,30 0,230 Z" fill="var(--brand-blue)"/>
    <path d="M0,230 Q350,30 700,80" fill="none" stroke="var(--brand-red)" stroke-width="12"/>
    <circle cx="190" cy="140" r="17" fill="var(--deep-blue)" stroke="var(--brand-red)" stroke-width="3"/>
    <circle cx="400" cy="83" r="17" fill="var(--deep-blue)" stroke="var(--brand-red)" stroke-width="3"/>
    <circle cx="570" cy="70" r="17" fill="var(--deep-blue)" stroke="var(--brand-red)" stroke-width="3"/>
    <g fill="#fff" font-family="Arimo, Arial, sans-serif" font-size="15" text-anchor="middle">
      <text x="190" y="145">1</text>
      <text x="400" y="88">2</text>
      <text x="570" y="75">3</text>
    </g>
  </svg>
  <p class="service service--red" style="left:190px; top:194px;">Sewer Drain Cleaning</p>
  <p class="service service--blue" style="left:400px; top:112px;">Maintenance</p>
  <p class="service service--red" style="left:570px; top:96px;">Trenchless Pipe Installs</p>
  <div class="wordmark">
    <span>Keystone<br>Plumbing</span>
    <span class="wordmark__dot"></span>
  </div>
</section>

<!-- Front of card: identity and contact -->
<section class="card card--front" aria-label="Card front with contact details">
  <svg class="card__art" viewBox="0 0 700 400" aria-hidden="true">
    <path d="M0,300 C180,205 430,290 700,215 V400 H0 Z" fill="var(--brand-red)"/>
    <path d="M0,318 C180,228 430,308 700,236 V400 H0 Z" fill="var(--brand-blue)"/>
  </svg>
  <div class="wordmark">
    <span>Keystone<br>Plumbing</span>
    <span class="wordmark__dot"></span>
  </div>
  <div class="person">
    <p class="person__name">MARCO DELANEY</p>
    <p class="person__role">Director</p>
  </div>
  <ul class="contact">
    <li>
      <svg viewBox="0 0 14 14"><rect x="3" y="0" width="8" height="14" rx="1.5"/></svg>
      0400-555-218
    </li>
    <li>
      <svg viewBox="0 0 14 14"><path d="M0,3 H14 V12 H0 Z"/></svg>
      m.delaney@keystoneplumb.com
    </li>
    <li>
      <svg viewBox="0 0 14 14"><circle cx="4" cy="10" r="3.2"/><circle cx="10" cy="4" r="3.2"/><rect x="5" y="5" width="4" height="4" transform="rotate(45 7 7)"/></svg>
      www.keystoneplumb.com
    </li>
  </ul>
</section>

</body>
</html>
```